Corporate Business Card

Very professional, Modern, Not to busy, include phone address email, website
(253) 617-4930, 18761 52nd Avenue S, Kent, WA 98047, martin@plumlinegroup.com, varkoworks.com

Target Market(s)

Manufacturing

Industry/Entity Type

Aero, machining, manufacturing, Off road racing

Contact Information for Business Card

Phone, address email, website

```html
<!DOCTYPE html>
<html lang="en">
<head>
<meta charset="utf-8">
<title>Varko Works – Business Card</title>
<link rel="stylesheet" href="https://fonts.googleapis.com/css2?family=Roboto:wght@400;500;700&family=Saira:wght@700&display=swap">
<style>
  :root {
    --navy: #2a3866;
    --navy-deep: #243260;
    --red: #c0272d;
    --paper: #eeeeee;
    --white: #f2f2f2;
    --stage: #2c2c2c;
  }
  * { margin: 0; padding: 0; box-sizing: border-box; }
  html, body { width: 1200px; height: 1138px; overflow: hidden; }
  body { background: var(--stage); font-family: "Roboto", sans-serif; position: relative; }

  .card {
    position: absolute;
    left: 276px;
    width: 620px;
    height: 375px;
    border-radius: 14px;
    box-shadow: 0 6px 14px rgba(0,0,0,.45);
  }

  /* Front */
  .card-front { top: 186px; background: var(--navy); }
  .card-front .brand-name {
    position: absolute; left: 0; right: 0; top: 120px;
    text-align: center;
    font-family: "Roboto", sans-serif; font-weight: 700;
    font-size: 72px; letter-spacing: 2px;
    color: var(--white);
  }
  .card-front .website {
    position: absolute; left: 0; right: 0; top: 328px;
    text-align: center;
    font-size: 16px; letter-spacing: 11px;
    color: var(--white);
  }
  .card-front .website .accent { color: var(--red); }

  /* Back */
  .card-back { top: 608px; background: linear-gradient(#f1f1f1, #e6e6e6); }
  .holder-name {
    position: absolute; left: 36px; top: 94px;
    font-family: "Saira", sans-serif; font-weight: 700;
    font-size: 27px; letter-spacing: -.3px;
    color: var(--navy);
  }
  .holder-name .surname { color: var(--red); }
  .rule {
    position: absolute; left: 36px; top: 128px;
    width: 422px; height: 2px; background: var(--navy);
  }
  .card-back .brand-name {
    position: absolute; right: 38px; top: 82px;
    font-family: "Roboto", sans-serif; font-weight: 700;
    font-size: 38px; letter-spacing: 1px;
    color: var(--navy);
  }
  .contact-list {
    position: absolute; left: 36px; top: 268px;
    list-style: none;
  }
  .contact-list li {
    display: flex; align-items: center;
    height: 24px; font-size: 16.5px; color: var(--navy);
  }
  .contact-list svg { width: 16px; height: 16px; margin-right: 16px; fill: var(--red); }
  .address {
    position: absolute; right: 66px; top: 294px;
    text-align: right; font-size: 16.5px; line-height: 24px; color: var(--navy);
  }
  .address-pin { position: absolute; right: 34px; top: 297px; width: 14px; height: 18px; fill: var(--red); }
</style>
</head>
<body>

<section class="card card-front">
  <div class="brand-name">VARKO WORKS</div>
  <div class="website">www.varko<span class="accent">works</span>.com</div>
</section>

<section class="card card-back">
  <div class="holder-name">MARTIN <span class="surname">HALE</span></div>
  <div class="rule"></div>
  <div class="brand-name">VARKO WORKS</div>

  <ul class="contact-list">
    <li>
      <svg viewBox="0 0 16 16" aria-hidden="true"><path d="M1 6c0-2 3-3 7-3s7 1 7 3v1h-4V5.5H5V7H1zM4 8h8l2 6H2z"/></svg>
      (253) 617-4930
    </li>
    <li>
      <svg viewBox="0 0 16 16" aria-hidden="true"><path d="M1 3h14v10H1zM2.5 4.5 8 9l5.5-4.5v1L8 10 2.5 5.5z" fill-rule="evenodd"/></svg>
      martin@plumlinegroup.com
    </li>
    <li>
      <svg viewBox="0 0 16 16" aria-hidden="true"><circle cx="8" cy="8" r="7"/><path d="M1 8h14M8 1v14M3 4h10M3 12h10" stroke="#eee" stroke-width="1" fill="none"/></svg>
      www.varkoworks.com
    </li>
  </ul>

  <div class="address">18761 52nd Avenue S,<br>Kent, WA 98047</div>
  <svg class="address-pin" viewBox="0 0 14 18" aria-hidden="true"><path d="M7 0a7 7 0 0 1 7 7c0 4-7 11-7 11S0 11 0 7a7 7 0 0 1 7-7zm0 4a3 3 0 1 0 0 6 3 3 0 0 0 0-6z" fill-rule="evenodd"/></svg>
</section>

</body>
</html>
```